Business Card for Coastal Tundrabridge Advisory

We need a business card for Coastal Tundrabridge Advisory. The company website address is provided below. The company logo is attached. We provide specialized permafrost services to the mining, transportation, and oil & gas industries. The card should be prepared for:
Matthias Korhonen, PhD.
Coastal Tundrabridge Advisory
PO Box 418259
Quillwater, Alaska 99642
Direct: +1-907-555-0143
Email: mkorhonen@tundrabridgeadvisory.example
Website: www.coastaltundrabridgeadvisory.example

```html
<!DOCTYPE html>
<html lang="en">
<head>
<meta charset="utf-8">
<title>Coastal Tundrabridge Advisory – Business Card</title>
<link rel="stylesheet" href="https://fonts.googleapis.com/css2?family=Roboto:ital,wght@0,300;0,400;0,500;0,700;1,300&family=Work+Sans:wght@300;700&display=swap">
<style>
  :root {
    --backdrop: #232323;
    --card: #111826;
    --ink: #ffffff;
    --ink-soft: #d9dde4;
  }
  * { box-sizing: border-box; margin: 0; padding: 0; }
  html, body {
    width: 1200px; height: 780px; overflow: hidden;
    background: var(--backdrop);
  }
  .canvas {
    width: 1200px; height: 780px;
    display: flex; align-items: center; justify-content: center; gap: 44px;
  }
  .card {
    position: relative;
    width: 525px; height: 300px;
    background: var(--card);
    color: var(--ink);
    font-family: "Roboto", Arial, sans-serif;
  }

  /* wordmark */
  .wordmark {
    display: flex; align-items: center; gap: 12px;
    font-family: "Roboto", Arial, sans-serif;
    font-weight: 500;
    text-transform: uppercase;
    letter-spacing: 0.18em;
    color: var(--ink);
    line-height: 1.25;
  }
  .wordmark__square {
    width: 14px; height: 14px; background: var(--ink); flex: none;
  }

  /* front */
  .card--front .holder {
    position: absolute; left: 26px; top: 24px;
  }
  .holder__name {
    font-family: "Work Sans", Arial, sans-serif;
    font-size: 26px; line-height: 1.05;
  }
  .holder__first { font-weight: 700; }
  .holder__last { font-weight: 300; }
  .holder__title {
    font-family: "Work Sans", Arial, sans-serif;
    font-weight: 700; font-size: 13px; margin-top: 3px;
  }
  .card--front .wordmark {
    position: absolute; right: 30px; top: 92px;
    font-size: 17px;
  }
  .contact {
    position: absolute; right: 26px; bottom: 20px;
    text-align: right; list-style: none;
    font-size: 13px; font-weight: 300; color: var(--ink-soft);
  }
  .contact__address { margin-bottom: 8px; line-height: 1.35; }
  .contact__line {
    display: flex; align-items: center; justify-content: flex-end;
    gap: 8px; line-height: 1.55;
  }
  .contact__icon { width: 13px; height: 13px; flex: none; }

  /* back */
  .card--back {
    display: flex; flex-direction: column; align-items: center;
    padding-top: 96px;
  }
  .card--back .wordmark { font-size: 21px; }
  .services {
    position: absolute; left: 0; right: 0; bottom: 26px;
    text-align: center;
  }
  .services__heading {
    font-weight: 700; font-size: 10px; letter-spacing: 0.02em;
    margin-bottom: 4px;
  }
  .services__text {
    font-style: italic; font-weight: 300; font-size: 10.5px; color: var(--ink-soft);
  }
</style>
</head>
<body>
<main class="canvas">

  <section class="card card--front" aria-label="Business card front">
    <header class="holder">
      <p class="holder__name"><span class="holder__first">Matthias</span> <span class="holder__last">Korhonen</span></p>
      <p class="holder__title">PhD</p>
    </header>

    <div class="wordmark">
      <span class="wordmark__square"></span>
      <span>Coastal Tundrabridge<br>Advisory</span>
    </div>

    <ul class="contact">
      <li class="contact__address">PO Box 418259<br>Quillwater, Alaska 99642</li>
      <li class="contact__line">+1-907-555-0143
        <svg class="contact__icon" viewBox="0 0 16 16" aria-hidden="true"><path fill="#fff" d="M3.6 1.5l2.2 2.6-1.3 1.6c.9 2 2.6 3.7 4.6 4.6l1.6-1.3 2.6 2.2-1.2 2.1C7.2 13.2 2.8 8.8 1.5 2.7z"/></svg>
      </li>
      <li class="contact__line">mkorhonen@tundrabridgeadvisory.example
        <svg class="contact__icon" viewBox="0 0 16 16" aria-hidden="true"><rect x="1" y="3" width="14" height="10" rx="1" fill="#fff"/><path d="M1.5 3.8L8 9l6.5-5.2" fill="none" stroke="#111826" stroke-width="1.3"/></svg>
      </li>
      <li class="contact__line">www.coastaltundrabridgeadvisory.example
        <svg class="contact__icon" viewBox="0 0 16 16" aria-hidden="true"><circle cx="8" cy="8" r="7" fill="#fff"/><path d="M1 8h14M8 1c-3 3.5-3 10.5 0 14M8 1c3 3.5 3 10.5 0 14" fill="none" stroke="#111826" stroke-width="1"/></svg>
      </li>
    </ul>
  </section>

  <section class="card card--back" aria-label="Business card back">
    <div class="wordmark">
      <span class="wordmark__square"></span>
      <span>Coastal Tundrabridge<br>Advisory</span>
    </div>
    <div class="services">
      <p class="services__heading">OUR SERVICES</p>
      <p class="services__text">We provide specialized permafrost services to the mining, transportation, and oil &amp; gas industries</p>
    </div>
  </section>

</main>
</body>
</html>
```